Web design required

1-We need a web design for existing company based in New Zealand
2-We build residential house and light commercial
3-We has in-house designer which allow us can provide interior design
4-We modeling project before site construction, which enable both client and construction team to visually analysis whole project,

Target Market(s)

middle class residential house market
Ref: http://www.parvellbuilders.co.nz/

Industry/Entity Type

Construction Company

Number of Pages Required

1 page

Font styles to use
Sans Serif
Other font styles liked:
• Such as : Central Gothic or similar which has more design taste

Colors

Designer to choose colors to be used in the design.

Requirements
Must have
• Front sheet, contact information, sample project

```html
<!DOCTYPE html>
<html lang="en">
<head>
<meta charset="utf-8">
<title>Kestrel Homes</title>
<link href="https://fonts.googleapis.com/css2?family=Montserrat:wght@400;600;700&family=Open+Sans:wght@400;600;700&display=swap" rel="stylesheet">
<style>
:root{
  --blue:#1b63b3;
  --blue-dark:#134a88;
  --navy:#1d2f4a;
  --ink:#2b2f36;
  --text:#6b7078;
  --grey-bg:#ececec;
  --line:#d9dbde;
  --white:#ffffff;
  --footer:#2a2e34;
  --footer-deep:#1f2227;
}
*{box-sizing:border-box;margin:0;padding:0}
html,body{width:1200px;height:3102px;overflow:hidden}
body{font-family:"Open Sans",Arial,sans-serif;color:var(--text);background:var(--white);font-size:14px;line-height:1.6}
.page{position:relative;width:1200px;height:3102px}

/* top bar */
.topbar{height:32px;background:var(--white);border-top:4px solid var(--blue);display:flex;justify-content:flex-end;align-items:center;gap:10px;padding-right:52px}
.topbar .chip{background:var(--blue);color:var(--white);font-size:11px;font-weight:600;padding:3px 12px;display:flex;align-items:center;gap:6px}
.topbar svg{width:11px;height:11px;fill:var(--white)}

/* header */
.header{height:80px;display:flex;align-items:center;justify-content:space-between;padding:0 52px 0 140px}
.brand{display:flex;align-items:center;gap:10px;font-family:"Montserrat",Arial,sans-serif;font-weight:700;font-size:22px;color:var(--navy);letter-spacing:1px}
.brand .mark{width:34px;height:34px;background:var(--navy)}
.nav{display:flex;align-items:center;gap:34px;font-family:"Montserrat",Arial,sans-serif;font-size:12px;font-weight:600;color:var(--ink)}
.nav .active{width:56px;height:56px;border-radius:50%;border:2px solid var(--line);display:flex;align-items:center;justify-content:center;color:var(--blue)}

/* hero */
.hero{position:relative;height:472px;background:linear-gradient(160deg,#9fc4ea 0%,#4e7fb4 35%,#1b355a 70%,#0d1b30 100%)}
.hero .arrow{position:absolute;top:200px;width:34px;height:34px;border-radius:50%;background:rgba(255,255,255,.35);display:flex;align-items:center;justify-content:center}
.hero .arrow svg{width:14px;height:14px;stroke:var(--white);fill:none;stroke-width:2.5}
.hero .prev{left:80px}.hero .next{right:80px}
.hero-caption{position:absolute;left:0;right:0;bottom:26px;text-align:center;color:var(--white);font-family:"Montserrat",Arial,sans-serif;font-weight:600;font-size:26px;letter-spacing:.5px}

/* about */
.about{height:432px;display:flex;gap:60px;padding:58px 144px 0 144px}
.about-copy{width:620px}
h2.title{font-family:"Montserrat",Arial,sans-serif;font-size:26px;font-weight:700;color:var(--ink);letter-spacing:.5px}
h2.title span{color:var(--blue)}
.about-copy p{margin-top:18px;font-size:13px;line-height:1.75}
.btn{display:inline-block;background:var(--blue);color:var(--white);font-family:"Montserrat",Arial,sans-serif;font-size:11px;font-weight:700;padding:8px 16px;letter-spacing:.5px}
.about-copy .btn{margin-top:22px}
.estimate{width:236px;border:1px solid var(--line);background:var(--white)}
.estimate h3{background:var(--footer);color:var(--white);font-family:"Montserrat",Arial,sans-serif;font-size:14px;font-weight:700;padding:14px 16px;letter-spacing:.5px;position:relative}
.estimate h3::after{content:"";position:absolute;left:50%;bottom:-10px;margin-left:-10px;border:10px solid transparent;border-bottom:0;border-top-color:var(--footer)}
.estimate form{padding:22px 12px 14px}
.field{height:30px;border:1px solid var(--line);margin-bottom:10px;font-size:11px;color:#a3a7ad;padding:6px 10px;display:flex;justify-content:space-between}
.field.area{height:56px}
.estimate .btn{display:block;text-align:center}

/* services */
.services{height:560px;background:var(--grey-bg);padding-top:52px}
.services h2.title,.projects h2.title,.testimonials h2.title{text-align:center}
.rule{width:60px;height:3px;background:var(--blue);margin:10px auto 0}
.cards{display:flex;gap:40px;justify-content:center;margin-top:36px}
.card{width:428px;height:416px;background:var(--white);border-bottom:4px solid var(--blue);text-align:center;position:relative}
.card .photo{height:220px}
.photo.house{background:linear-gradient(180deg,#6f9fd0 0%,#c9d7e4 55%,#6a7a58 100%)}
.photo.tower{background:linear-gradient(180deg,#bcd6ef 0%,#dfe8f1 50%,#8e9aa8 100%)}
.card .icon{position:absolute;left:50%;top:186px;margin-left:-34px;width:68px;height:68px;border-radius:50%;background:var(--blue);border:4px solid var(--white);display:flex;align-items:center;justify-content:center}
.card .icon svg{width:30px;height:30px;fill:var(--white)}
.card h3{margin-top:52px;font-family:"Montserrat",Arial,sans-serif;font-size:17px;font-weight:700;color:var(--ink)}
.card p{margin:10px 48px 0;font-size:12px;line-height:1.65}
.card .btn{margin-top:16px}

/* projects */
.projects{height:720px;padding-top:40px}
.hexes{display:block;margin-top:18px}

/* testimonials */
.testimonials{height:468px;background:var(--grey-bg);padding-top:48px;position:relative}
.people{display:flex;justify-content:center;gap:70px;margin-top:32px}
.person{text-align:center;width:90px}
.avatar{width:88px;height:88px;border-radius:50%;border:4px solid var(--white);background:linear-gradient(160deg,#c79a7d,#7c5a48);box-shadow:0 0 0 1px var(--line)}
.person.selected .avatar{box-shadow:0 0 0 3px var(--blue)}
.person .name{margin-top:8px;font-size:11px;font-weight:600;color:var(--ink)}
.person.selected .name{color:var(--blue)}
.testimonials .arrow{position:absolute;top:206px;width:20px;height:20px}
.testimonials .arrow svg{width:20px;height:20px;stroke:#9aa0a7;fill:none;stroke-width:2.5}
.testimonials .prev{left:250px}.testimonials .next{right:250px}
.quote{width:884px;margin:40px auto 0;background:var(--white);padding:22px 40px;font-size:12px;line-height:1.75;text-align:center;position:relative}
.quote .mark{position:absolute;left:14px;top:10px;font-family:"Montserrat",Arial,sans-serif;font-size:30px;color:var(--blue);line-height:1}

/* footer */
.footer{height:322px;background:linear-gradient(180deg,var(--footer) 0%,#33373e 70%,var(--footer-deep) 100%);color:#c4c8ce;position:relative}
.footer-cols{display:flex;padding:40px 0 0 144px;gap:0}
.footer h4{font-family:"Montserrat",Arial,sans-serif;font-size:12px;font-weight:700;color:var(--white);letter-spacing:.5px;margin-bottom:14px}
.col-links{width:208px}
.col-links li{list-style:none;font-size:11px;margin-bottom:6px;display:flex;align-items:center;gap:8px}
.col-links li::before{content:"";width:5px;height:5px;background:var(--blue);display:inline-block}
.col-contact{width:248px}
.col-contact li{list-style:none;font-size:11px;margin-bottom:9px;display:flex;gap:8px;align-items:flex-start}
.col-contact svg{width:12px;height:12px;fill:var(--white);flex:none;margin-top:2px}
.col-map{width:240px}
.map{width:230px;height:136px;background:linear-gradient(135deg,#e9ece8,#cfd8d2)}
.footer-brand{position:absolute;right:150px;top:60px;text-align:center}
.footer-brand .name{font-family:"Montserrat",Arial,sans-serif;font-weight:700;font-size:16px;color:var(--white);letter-spacing:1px}
.social{display:flex;gap:8px;margin-top:14px;justify-content:center}
.social span{width:20px;height:20px;border-radius:50%;background:var(--blue)}
.social span:last-child{background:#c9302c}
.copyright{position:absolute;left:0;right:0;bottom:0;height:38px;background:var(--footer-deep);text-align:center;font-size:11px;line-height:38px;color:#b0b5bb}
</style>
</head>
<body>
<div class="page">

  <div class="topbar">
    <span class="chip"><svg viewBox="0 0 24 24"><path d="M6.6 10.8a15 15 0 006.6 6.6l2.2-2.2a1 1 0 011-.25 11.4 11.4 0 003.6.57 1 1 0 011 1V20a1 1 0 01-1 1A17 17 0 013 4a1 1 0 011-1h3.5a1 1 0 011 1c0 1.25.2 2.45.57 3.57a1 1 0 01-.25 1z"/></svg>(09) 555 0148</span>
    <span class="chip"><svg viewBox="0 0 24 24"><path d="M2 5h20v14H2zm2 2v.5l8 5 8-5V7z"/></svg>info@kestrelhomes.example</span>
  </div>

  <header class="header">
    <div class="brand"><span class="mark"></span>KESTREL HOMES</div>
    <nav class="nav">
      <span class="active">HOME</span>
      <span>ABOUT US</span>
      <span>SERVICES</span>
      <span>RECENT PROJECTS</span>
      <span>CONTACT US</span>
    </nav>
  </header>

  <section class="hero" role="img" aria-label="Photo looking up at glass office towers against a blue sky">
    <span class="arrow prev"><svg viewBox="0 0 16 16"><path d="M10 3L5 8l5 5"/></svg></span>
    <span class="arrow next"><svg viewBox="0 0 16 16"><path d="M6 3l5 5-5 5"/></svg></span>
    <p class="hero-caption">We Build Residential House And Light Commercial</p>
  </section>

  <section class="about">
    <div class="about-copy">
      <h2 class="title">ABOUT <span>KESTREL HOMES</span></h2>
      <p>We are a New Zealand building company creating quality family homes and light commercial spaces. Our in-house designer shapes every interior with care, so each room feels right from the first sketch to the final handover. Before we break ground we model the whole project in 3D, letting clients and our site team walk through the build, spot details early and keep every stage on time and on budget. From first meeting to final key, we stay with you the whole way.</p>
      <span class="btn">READ MORE</span>
    </div>
    <aside class="estimate">
      <h3>GET A FREE ESTIMATE</h3>
      <form>
        <div class="field">Name</div>
        <div class="field">Email</div>
        <div class="field">Phone</div>
        <div class="field">Service <span>&#9662;</span></div>
        <div class="field area">Message</div>
        <span class="btn">SUBMIT</span>
      </form>
    </aside>
  </section>

  <section class="services">
    <h2 class="title">OUR <span>SERVICES</span></h2>
    <div class="rule"></div>
    <div class="cards">
      <article class="card">
        <div class="photo house" role="img" aria-label="Photo of a modern two-storey family house at dusk"></div>
        <span class="icon"><svg viewBox="0 0 24 24"><path d="M12 3l10 9h-3v9h-5v-6h-4v6H5v-9H2z"/></svg></span>
        <h3>RESIDENTIAL SERVICES</h3>
        <p>We design and build warm, practical family homes for the middle class market, with interiors planned by our own designer and finished to a high standard.</p>
        <span class="btn">READ MORE</span>
      </article>
      <article class="card">
        <div class="photo tower" role="img" aria-label="Photo of modern commercial office buildings"></div>
        <span class="icon"><svg viewBox="0 0 24 24"><path d="M3 21V8h6V3h12v18h-7v-4h-3v4zm3-10v2h2v-2zm0 4v2h2v-2zm6-8v2h2V7zm4 0v2h2V7zm-4 4v2h2v-2zm4 0v2h2v-2z"/></svg></span>
        <h3>COMMERCIAL SERVICES</h3>
        <p>We deliver light commercial buildings such as offices, shops and small workspaces, modelled in full before construction so every detail is clear to all.</p>
        <span class="btn">READ MORE</span>
      </article>
    </div>
  </section>

  <section class="projects">
    <h2 class="title">RECENT <span>PROJECTS</span></h2>
    <div class="rule"></div>
    <svg class="hexes" width="1200" height="600" viewBox="0 0 1200 600">
      <defs>
        <linearGradient id="g-house" x1="0" y1="0" x2="0" y2="1"><stop offset="0" stop-color="#8fb6de"/><stop offset=".55" stop-color="#c7b8a2"/><stop offset="1" stop-color="#6f8758"/></linearGradient>
        <linearGradient id="g-tower" x1="0" y1="0" x2="0" y2="1"><stop offset="0" stop-color="#a9c9ea"/><stop offset=".6" stop-color="#5f86b2"/><stop offset="1" stop-color="#34506f"/></linearGradient>
      </defs>
      <g stroke="#1b63b3" stroke-width="6">
        <polygon role="img" aria-label="Project photo: suburban family home" fill="url(#g-house)" points="248,20 352,80 352,200 248,260 144,200 144,80"/>
        <polygon role="img" aria-label="Project photo: modern two-storey house" fill="url(#g-house)" points="492,20 596,80 596,200 492,260 388,200 388,80"/>
        <polygon role="img" aria-label="Project photo: family home with garden" fill="url(#g-house)" points="732,20 836,80 836,200 732,260 628,200 628,80"/>
        <polygon role="img" aria-label="Project photo: glass commercial building" fill="url(#g-tower)" points="960,20 1064,80 1064,200 960,260 856,200 856,80"/>
        <polygon role="img" aria-label="Project photo: office building exterior" fill="url(#g-tower)" points="380,336 484,396 484,516 380,576 276,516 276,396"/>
        <polygon role="img" aria-label="Project photo: contemporary family house" fill="url(#g-house)" points="840,336 944,396 944,516 840,576 736,516 736,396"/>
      </g>
      <text x="610" y="463" text-anchor="middle" font-family="Montserrat, Arial, sans-serif" font-weight="700" font-size="24" fill="#1d2f4a" letter-spacing="1">KESTREL HOMES</text>
    </svg>
  </section>

  <section class="testimonials">
    <h2 class="title">CLIENT <span>TESTIMONIALS</span></h2>
    <div class="rule"></div>
    <span class="arrow prev"><svg viewBox="0 0 16 16"><path d="M10 3L5 8l5 5"/></svg></span>
    <span class="arrow next"><svg viewBox="0 0 16 16"><path d="M6 3l5 5-5 5"/></svg></span>
    <div class="people">
      <div class="person selected"><div class="avatar" role="img" aria-label="Client portrait photo"></div><p class="name">Anna Hartley</p></div>
      <div class="person"><div class="avatar" role="img" aria-label="Client portrait photo"></div><p class="name">Mira Collins</p></div>
      <div class="person"><div class="avatar" role="img" aria-label="Client portrait photo"></div><p class="name">Mark Davey</p></div>
      <div class="person"><div class="avatar" role="img" aria-label="Client portrait photo"></div><p class="name">Mike Rowan</p></div>
    </div>
    <blockquote class="quote"><span class="mark">&ldquo;</span>Kestrel Homes built our new family home exactly as planned. Seeing the full 3D model before work started gave us real confidence, and the team kept us informed at every step. We could not be happier with the result and would gladly recommend them.</blockquote>
  </section>

  <footer class="footer">
    <div class="footer-cols">
      <div class="col-links">
        <h4>QUICK LINKS</h4>
        <ul>
          <li>Home</li><li>About Us</li><li>Services</li><li>Recent Projects</li><li>Contact Us</li>
        </ul>
      </div>
      <div class="col-contact">
        <h4>CONTACT DETAILS</h4>
        <ul>
          <li><svg viewBox="0 0 24 24"><path d="M12 2a7 7 0 00-7 7c0 5 7 13 7 13s7-8 7-13a7 7 0 00-7-7zm0 9.5A2.5 2.5 0 1112 6.5a2.5 2.5 0 010 5z"/></svg><span>KESTREL HOMES<br>24 Harbour View Road, Auckland</span></li>
          <li><svg viewBox="0 0 24 24"><path d="M6.6 10.8a15 15 0 006.6 6.6l2.2-2.2a1 1 0 011-.25 11.4 11.4 0 003.6.57 1 1 0 011 1V20a1 1 0 01-1 1A17 17 0 013 4a1 1 0 011-1h3.5a1 1 0 011 1c0 1.25.2 2.45.57 3.57a1 1 0 01-.25 1z"/></svg>(09) 555 0148</li>
          <li><svg viewBox="0 0 24 24"><path d="M2 5h20v14H2zm2 2v.5l8 5 8-5V7z"/></svg>info@kestrelhomes.example</li>
        </ul>
      </div>
      <div class="col-map">
        <h4>LOCATION MAP</h4>
        <div class="map" role="img" aria-label="Street map showing the office location"></div>
      </div>
    </div>
    <div class="footer-brand">
      <p class="name">KESTREL HOMES</p>
      <div class="social"><span></span><span></span><span></span><span></span></div>
    </div>
    <p class="copyright">Copyright &copy; 2017 KESTREL HOMES. All Rights Reserved.</p>
  </footer>

</div>
</body>
</html>
```